Web Design Project

Please take a look at my current aged website www.talvikhrconsulting.com and my newly designed logo and business cards. I would like a new fresh updated look to my website and my new designs incorporated.
Updates

  Good Morning Everyone

Due to an Austrralian licencing issue I have had to have my logo slightly redesigned.

Would you please be able to look at the newly uploaded files and revise your designs.

Thanks so much.  I am very happy with the calibre and quality of the designs so far.

kind Regards

Marla

Industry/Entity Type

Business

Requirements
Must have
• the exisiting pages and fresh new graphics and a real commitment to my palette of lime green, turqouise and black.

```html
<!DOCTYPE html>
<html lang="en">
<head>
<meta charset="UTF-8">
<title>Talvik HR Consulting – Our Fees</title>
<link href="https://fonts.googleapis.com/css2?family=Arimo:wght@400&family=Roboto+Condensed:wght@300;400&family=Open+Sans:wght@400&display=swap" rel="stylesheet">
<style>
  :root {
    --backdrop: #8c8c8c;
    --page: #ffffff;
    --header-light: #f4f4f4;
    --header-dark: #c9c9c9;
    --ink: #111111;
    --muted: #8a8a8a;
    --nav-ink: #555555;
    --lime: #6db33f;
    --lime-pale: #d3e4c6;
    --turquoise: #2aa9d2;
    --ring: #c4c4c4;
    --hub: #e6e6e6;
    --photo-a: #5a6e86;
    --photo-b: #d9dee6;
  }
  * { margin: 0; padding: 0; box-sizing: border-box; }
  html, body { width: 1200px; height: 900px; overflow: hidden; }
  body {
    background: var(--backdrop);
    position: relative;
    font-family: "Arimo", Arial, sans-serif;
    color: var(--ink);
  }
  .page {
    position: absolute;
    left: 179px; top: 15px;
    width: 847px; height: 885px;
    background: var(--page);
    box-shadow: 0 0 18px rgba(0,0,0,0.55);
    overflow: hidden;
  }
  .page__stripe {
    position: absolute; left: 0; top: 0;
    width: 28px; height: 100%;
    background: linear-gradient(to bottom, #e4eedd 0%, #a9d08c 40%, var(--lime) 75%, var(--lime) 100%);
  }
  .page__header-band { position: absolute; left: 28px; top: 0; }
  .brand-mark {
    position: absolute; left: 58px; top: 42px;
    width: 120px; height: 120px;
    border-radius: 50%;
    border: 5px solid var(--turquoise);
    display: flex; align-items: center; justify-content: center;
    font-family: "Arimo", Arial, sans-serif;
    font-size: 22px; color: var(--ink);
  }
  .brand-title {
    position: absolute; left: 213px; top: 38px;
    font-size: 41px; font-weight: 400; letter-spacing: -0.3px;
  }
  .brand-tagline {
    position: absolute; left: 287px; top: 86px;
    font-size: 16.5px; color: var(--muted);
  }
  .content { position: absolute; left: 98px; top: 316px; }
  .content__heading {
    font-family: "Open Sans", Arial, sans-serif;
    font-size: 25px; font-weight: 400; letter-spacing: -0.3px;
  }
  .content__photo {
    margin-top: 22px;
    width: 224px; height: 150px;
    background: linear-gradient(135deg, var(--photo-b) 0%, #b7c2d0 45%, var(--photo-a) 100%);
  }
  .content__text {
    font-size: 18.6px; line-height: 25.6px;
    margin-top: 13px;
  }
  .content__text + .content__text { margin-top: 51px; }
  .site-nav {
    position: absolute; left: 0; top: 0; width: 1200px; height: 900px;
    pointer-events: none;
    font-family: "Roboto Condensed", "Arial Narrow", sans-serif;
    font-weight: 300; font-size: 24px; color: var(--nav-ink);
  }
  .site-nav__item { position: absolute; white-space: nowrap; }
  .site-nav__item--home { right: 294px; top: 190px; }
  .site-nav__item--services { right: 322px; top: 233px; }
  .site-nav__item--consultants { right: 334px; top: 280px; }
  .site-nav__item--fees {
    left: 776px; top: 327px; width: 125px; height: 35px;
    background: var(--lime-pale); border-radius: 6px;
    padding-left: 19px; line-height: 35px; color: #333;
  }
  .site-nav__item--contact { left: 916px; top: 402px; }
  .nav-wheel { position: absolute; left: 854px; top: 166px; }
</style>
</head>
<body>
  <div class="page">
    <div class="page__stripe"></div>
    <svg class="page__header-band" width="819" height="300" viewBox="0 0 819 300" aria-hidden="true">
      <defs>
        <linearGradient id="bandFill" x1="0" y1="0" x2="0" y2="1">
          <stop offset="0" stop-color="#fafafa"/>
          <stop offset="1" stop-color="#c6c6c6"/>
        </linearGradient>
      </defs>
      <path d="M0 0 H819 V112 C560 145 250 190 0 268 Z" fill="url(#bandFill)"/>
      <path d="M0 268 C250 190 560 145 819 112" fill="none" stroke="#ffffff" stroke-width="3"/>
    </svg>
    <div class="brand-mark">Talvik</div>
    <h1 class="brand-title">Talvik HR Consulting</h1>
    <p class="brand-tagline">Outsourced Human Resources Solutions and Stragedies</p>

    <main class="content">
      <h2 class="content__heading">Our Fees</h2>
      <div class="content__photo" role="img" aria-label="Photo of business people shaking hands at a meeting"></div>
      <p class="content__text">Our highly competitive fees will be tailored to suit your<br>organisation’s individual needs.&nbsp; Generally the Consultant’s<br>time will be charged at an hourly rate however some<br>projects will require the Consultant to work on a retainer<br>or an agreed fixed fee for a specific project and these<br>rates may be negotiated.</p>
      <p class="content__text">Fees, Terms and Conditions and a Service Level Agreement<br>will be discussed and negotiated at your initial no-obligation<br>on-site consultation.</p>
    </main>
  </div>

  <svg class="nav-wheel" width="260" height="260" viewBox="0 0 260 260" aria-hidden="true">
    <defs>
      <radialGradient id="hubFill" cx="0.45" cy="0.4" r="0.6">
        <stop offset="0" stop-color="#f0f0f0"/>
        <stop offset="1" stop-color="#d8d8d8"/>
      </radialGradient>
      <filter id="wheelShadow" x="-20%" y="-20%" width="140%" height="140%">
        <feDropShadow dx="3" dy="4" stdDeviation="4" flood-opacity="0.4"/>
      </filter>
    </defs>
    <circle cx="130" cy="130" r="108" fill="#e9e9e9" stroke="#bdbdbd" stroke-width="2" filter="url(#wheelShadow)"/>
    <circle cx="130" cy="130" r="92" fill="none" stroke="var(--ring)" stroke-width="24"/>
    <g fill="none" stroke-width="16">
      <circle cx="130" cy="130" r="92" stroke="var(--turquoise)" stroke-dasharray="45 600" transform="rotate(-128 130 130)"/>
      <circle cx="130" cy="130" r="92" stroke="var(--turquoise)" stroke-dasharray="38 600" transform="rotate(-155 130 130)"/>
      <circle cx="130" cy="130" r="92" stroke="var(--turquoise)" stroke-dasharray="32 600" transform="rotate(-178 130 130)"/>
      <circle cx="130" cy="130" r="92" stroke="var(--lime)" stroke-dasharray="37 600" transform="rotate(155 130 130)"/>
      <circle cx="130" cy="130" r="92" stroke="var(--turquoise)" stroke-dasharray="112 600" transform="rotate(55 130 130)"/>
    </g>
    <circle cx="130" cy="130" r="83" fill="#f2f2f2"/>
    <circle cx="124" cy="122" r="70" fill="url(#hubFill)"/>
  </svg>

  <nav class="site-nav">
    <span class="site-nav__item site-nav__item--home">Home</span>
    <span class="site-nav__item site-nav__item--services">Our Services</span>
    <span class="site-nav__item site-nav__item--consultants">Our Consultants</span>
    <span class="site-nav__item site-nav__item--fees">Our Fees</span>
    <span class="site-nav__item site-nav__item--contact">Contact Us</span>
  </nav>
</body>
</html>
```